Design a Google site for a travel agency

I own a travel agency and I would like to have a Google site built for my company called Harborquestjourneys.com by Bright Path Holidays. Our specialty Cruising and adventure. We create a lot of custom tour of Europe and Peru. Our Adventure tours targets mainly women from 25 to 65. I would like to site especially the cruise to appeal to family but also upscale more expensive upscale clientele.
Updates

I would like to shift away from create a new site with multiple pages to one simple Google Site page with a Contact us page and testimonials. The sites theme is Harborquest Journeys. We specialize in selling cruises and building custom travel tours around the world.

Target Market(s)

Cruisers and adventure travelers for women from 25 to 70

Industry/Entity Type

travel industry with a focus on cruising and adventure travel

Coding

Coded - Design and coding required

Number of Pages Required

5+ page

Font styles to use
Serif
Sans Serif

Requirements
Must have
• Home page, Cruise, Adventure Tours, Testimonials, About Us
Nice to have
• Auto place https://www.brightpathholidays.ca/offers into the site.
Should not have
• beach resorts

```html
<!DOCTYPE html>
<html lang="en">
<head>
<meta charset="utf-8">
<title>Harborquest Journeys — Cruise & Adventure Tours</title>
<link href="https://fonts.googleapis.com/css2?family=Poppins:wght@400;500;600;700&family=Nunito+Sans:wght@400;600&display=swap" rel="stylesheet">
<style>
:root{
  --ink:#1d1d1d;
  --black:#000;
  --white:#fff;
  --cream:#f6f4ef;
  --orange:#ea7a23;
  --teal:#2a8fb2;
  --teal-light:#5ab4d8;
  --green:#1f6b45;
  --grey:#6b6b6b;
  --line:#c9c9c9;
}
*{box-sizing:border-box;margin:0;padding:0}
html,body{width:1200px;height:4926px;overflow:hidden;background:var(--white)}
body{font-family:"Nunito Sans",sans-serif;color:var(--ink)}
.page{position:relative;width:1200px;height:4926px;overflow:hidden}
.abs{position:absolute}
.display{font-family:"Poppins",sans-serif}

/* header */
.site-header{position:absolute;top:38px;left:0;width:1200px;height:67px;background:var(--black)}
.brand{position:absolute;left:14px;top:22px;font-family:"Poppins",sans-serif;font-weight:600;font-size:16px;color:var(--orange);letter-spacing:1px}
.main-nav{position:absolute;left:662px;top:23px;display:flex;gap:24px;font-family:"Poppins",sans-serif;font-size:16px;color:var(--white)}
.main-nav .active{color:#f0c9a0}
.quote-outline{position:absolute;left:1028px;top:15px;width:137px;height:36px;border:2px solid var(--white);border-radius:18px;color:var(--white);font-family:"Poppins",sans-serif;font-size:11px;display:flex;align-items:center;justify-content:center}

/* hero */
.hero{position:absolute;top:105px;left:0;width:1200px;height:726px;background:linear-gradient(180deg,#8fa7b4 0%,#5b7f6a 30%,#3f6f86 55%,#2e6b8c 75%,#4d7a3c 100%)}
.hero-title{position:absolute;left:277px;top:148px;font-family:"Poppins",sans-serif;font-weight:700;font-size:64px;line-height:62px;color:var(--white)}
.hero-bar{position:absolute;left:235px;top:298px;width:732px;height:67px;background:var(--white);border-radius:34px}
.hero-bar span{position:absolute;left:42px;top:21px;font-family:"Poppins",sans-serif;font-size:20px;color:var(--ink)}
.btn-teal{background:var(--teal);color:var(--white);font-family:"Poppins",sans-serif;font-weight:600;border-radius:24px;display:flex;align-items:center;justify-content:center}
.hero-bar .btn-teal{position:absolute;left:554px;top:13px;width:163px;height:41px;font-size:13px}
.chat{position:absolute;left:1028px;top:401px;width:157px;height:42px;background:var(--teal);color:var(--white);font-size:14px;display:flex;align-items:center;gap:8px;padding-left:16px}
.chat i{width:22px;height:22px;border-radius:50%;border:2px solid var(--white)}

/* why */
.section-title{font-family:"Poppins",sans-serif;font-size:27px;color:var(--ink)}
.tile{position:absolute;overflow:hidden}
.tile-text{position:absolute;font-family:"Poppins",sans-serif;font-weight:700;color:var(--white)}
.orange-box{background:var(--orange)}
.dot{position:absolute;width:30px;height:30px;border-radius:50%;background:var(--orange)}
.cta-line{position:absolute;font-family:"Poppins",sans-serif;font-size:28px}
.btn-green{position:absolute;background:var(--green);color:var(--white);font-family:"Poppins",sans-serif;font-size:12px;border-radius:22px;display:flex;align-items:center;justify-content:center}

/* steps */
.cream{position:absolute;left:0;width:1200px;background:var(--cream)}
.step-num{position:absolute;left:126px;font-size:13px;color:var(--green)}
.step-title{position:absolute;left:124px;font-family:"Poppins",sans-serif;font-size:38px;color:var(--ink)}
.step-text{position:absolute;left:127px;width:340px;font-size:13px;line-height:23px;color:#333}
.faded{opacity:.18}

/* cards */
.card{position:absolute;top:2775px;width:346px;height:258px;border:2px solid #e4e4e4}
.card-text{position:absolute;left:0;right:0;text-align:center;font-family:"Poppins",sans-serif;font-weight:500;font-size:56px;line-height:56px;color:var(--white)}

/* testimonials */
.testimonials{position:absolute;top:3751px;left:0;width:1200px;height:520px;background:linear-gradient(180deg,#dfe7e6 0%,#e7ecea 55%,#c9dbe0 100%)}
.quote{position:absolute;width:300px;text-align:center}
.avatar{width:134px;height:134px;border-radius:50%;background:#cfcfcf;margin:80px auto 0}
.q-name{margin-top:50px;font-size:19px;color:var(--teal-light)}
.q-text{margin:16px auto 0;width:220px;font-size:13px;line-height:24px;color:#333}
.q-mark{margin-top:40px;font-family:"Poppins",sans-serif;font-weight:700;font-size:56px;line-height:40px;color:#2f86e0}

/* footer */
.footer-brand{position:absolute;left:38px;top:4384px;font-family:"Poppins",sans-serif;font-weight:500;font-size:21px;color:var(--orange);letter-spacing:1px}
.contact-row{position:absolute;left:26px;display:flex;align-items:center;gap:24px;font-size:13px}
.icon{width:44px;height:44px;border-radius:50%;background:var(--black);display:flex;align-items:center;justify-content:center}
.social{position:absolute;top:4756px;width:26px;height:26px;border-radius:50%}
.foot-nav{position:absolute;left:464px;top:4353px;width:295px;font-family:"Poppins",sans-serif;font-size:11px;text-align:center}
.foot-nav a{display:block;height:67px;line-height:55px;color:var(--ink);text-decoration:none}
.foot-nav a.active{background:var(--teal);color:var(--white);height:55px;margin-bottom:12px;font-weight:600}
.form-title{position:absolute;left:925px;top:4374px;font-family:"Poppins",sans-serif;font-size:20px}
.label{position:absolute;font-size:8px;color:#444}
.field{position:absolute;height:23px;background:var(--cream);border-bottom:1px solid #888}
.submit{position:absolute;left:904px;top:4680px;width:84px;height:26px;font-size:13px}
</style>
</head>
<body>
<div class="page">

  <header class="site-header">
    <div class="brand">HARBORQUEST JOURNEYS</div>
    <nav class="main-nav"><span class="active">Home</span><span>Cruises</span><span>Adventures Tours</span><span>More</span></nav>
    <div class="quote-outline">Request a Quote</div>
  </header>

  <section class="hero" role="img" aria-label="Fjord with cruise ships between steep green mountains">
    <h1 class="hero-title">Cruise &amp;<br>Adventure Tours</h1>
    <div class="hero-bar"><span>Travel The Way You Want It</span><div class="btn-teal">Request a Quote</div></div>
    <div class="chat"><i></i>Let's Chat!</div>
  </section>

  <h2 class="section-title abs" style="left:48px;top:922px">Why Book With Us</h2>

  <div class="tile" style="left:31px;top:1143px;width:370px;height:550px;background:linear-gradient(180deg,#c9cfcc 0%,#7e9aa0 45%,#1f5a61 100%)" role="img" aria-label="Aerial view of rocky coast and turquoise sea">
    <div class="tile-text" style="left:29px;top:140px;font-size:78px;line-height:92px">Long<br>voyage</div>
  </div>
  <div class="tile" style="left:417px;top:1143px;width:365px;height:550px;background:linear-gradient(180deg,#3d7f93 0%,#8ab7c0 40%,#e7b06a 55%,#3f7f96 100%)" role="img" aria-label="Infinity pool edge with ladder at sunset">
    <div class="tile-text" style="left:32px;top:210px;font-size:72px;line-height:80px">Find<br>yourself</div>
  </div>
  <div class="tile" style="left:782px;top:1143px;width:244px;height:304px;background:linear-gradient(180deg,#3f8fd1 0%,#d9e4ec 50%,#2d6ea8 100%)" role="img" aria-label="Bow of a white cruise ship at sea">
    <div class="tile-text" style="left:40px;top:40px;font-size:36px;line-height:42px;opacity:.6">Trip<br>Advice</div>
  </div>
  <div class="tile orange-box" style="left:801px;top:1462px;width:244px;height:231px">
    <div class="tile-text" style="left:18px;top:26px;font-size:37px;line-height:42px">Plan Your<br>Trip With<br>Us</div>
  </div>

  <div class="dot" style="left:393px;top:1785px"></div>
  <div class="cta-line" style="left:441px;top:1778px">Get to Know Us</div>
  <div class="btn-green" style="left:669px;top:1779px;width:138px;height:44px">Learn More</div>

  <section class="cream" style="top:1907px;height:850px"></section>
  <h2 class="section-title abs" style="left:0;width:1200px;text-align:center;top:2025px">Book Your Trip in 3 Easy Steps</h2>

  <div class="step-num" style="top:2169px">01</div>
  <h3 class="step-title" style="top:2193px">Reserve Your Ride</h3>
  <p class="step-text" style="top:2248px">I'm a paragraph. Click here to add your own text and edit me. Let your users get to know you.</p>
  <div class="step-num" style="top:2352px">02</div>
  <h3 class="step-title" style="top:2375px">Plan Your Trip</h3>
  <p class="step-text" style="top:2430px">I'm a paragraph. Click here to add your own text and edit me. Let your users get to know you.</p>
  <h3 class="step-title" style="top:2560px;height:28px;overflow:hidden"><span style="position:relative;top:-22px">Hit the Road</span></h3>
  <p class="step-text faded" style="top:2636px">I'm a paragraph. Click here to add your own text and edit me. Let your users get to know you.</p>

  <div class="abs" style="left:743px;top:2180px;width:348px;height:537px;background:linear-gradient(180deg,#2a9bb5 0%,#5a8da0 40%,#3b6f82 65%,#c98a2b 85%,#2c5a6b 100%)" role="img" aria-label="Paraglider above layered mountain ridges"></div>
  <div class="abs" style="left:648px;top:2190px;width:237px;height:237px;background:linear-gradient(135deg,#d8dbdd 0%,#9aa3a6 50%,#3c3c3c 100%)" role="img" aria-label="Traveller stepping out of a camper van door"></div>

  <div class="card" style="left:44px;background:linear-gradient(180deg,#6aa6d6 0%,#dfe9f0 50%,#2a7bb8 100%)" role="img" aria-label="Cruise ship on open ocean"><div class="card-text" style="top:100px">Cruise</div></div>
  <div class="card" style="left:428px;background:linear-gradient(160deg,#1f6f83 0%,#3c8aa0 50%,#c88a36 80%,#2e5a66 100%)" role="img" aria-label="Mountain ridge above a sea of clouds"><div class="card-text" style="top:80px">Adventure<br>Travel</div></div>
  <div class="card" style="left:810px;background:linear-gradient(160deg,#3e6d3a 0%,#6fa6b8 45%,#1f8fb0 100%)" role="img" aria-label="Limestone cliffs over turquoise water"><div class="card-text" style="top:82px">Custom<br>Tours</div></div>

  <section class="cream" style="top:3109px;height:216px"></section>
  <div class="dot" style="left:320px;top:3199px"></div>
  <div class="cta-line" style="left:368px;top:3193px">Find Your Next Road Trip</div>
  <div class="btn-teal abs" style="left:715px;top:3192px;width:164px;height:44px;font-size:12px;font-weight:500">Discover Trip Ideas</div>

  <div class="abs" style="left:0;top:3325px;width:1200px;height:426px;background:linear-gradient(180deg,#28b5b8 0%,#1fa6b0 50%,#2bb8b5 100%)" role="img" aria-label="Aerial view of a river cruise ship on turquoise water"></div>

  <section class="testimonials" role="img" aria-label="Faded tropical pool with palm trees behind customer quotes">
    <div class="quote" style="left:50px"><div class="avatar" role="img" aria-label="Customer portrait"></div><div class="q-name">Name, Title</div><p class="q-text">Share the amazing things customers are saying about your business. Double click, or click Edit Text to make it yours.</p><div class="q-mark">”</div></div>
    <div class="quote" style="left:454px"><div class="avatar" role="img" aria-label="Customer portrait"></div><div class="q-name">Name, Title</div><p class="q-text">Share the amazing things customers are saying about your business. Double click, or click Edit Text to make it yours.</p><div class="q-mark">”</div></div>
    <div class="quote" style="left:855px"><div class="avatar" role="img" aria-label="Customer portrait"></div><div class="q-name">Name, Title</div><p class="q-text">Share the amazing things customers are saying about your business. Double click, or click Edit Text to make it yours.</p><div class="q-mark">”</div></div>
  </section>

  <footer>
    <div class="footer-brand">HARBORQUEST JOURNEYS</div>
    <div class="contact-row" style="top:4496px"><span class="icon"><svg width="20" height="20" viewBox="0 0 24 24"><path d="M12 2a7 7 0 0 0-7 7c0 5 7 13 7 13s7-8 7-13a7 7 0 0 0-7-7z" fill="none" stroke="#fff" stroke-width="2"/><circle cx="12" cy="9" r="2.5" fill="#fff"/></svg></span>14 Linden Row, Fairhaven, NB E3A 2K5, Canada</div>
    <div class="contact-row" style="top:4578px"><span class="icon"><svg width="20" height="20" viewBox="0 0 24 24"><rect x="3" y="6" width="18" height="12" rx="1" fill="none" stroke="#fff" stroke-width="2"/><path d="M3 7l9 6 9-6" fill="none" stroke="#fff" stroke-width="2"/></svg></span>hello@harborquestjourneys.ca</div>
    <div class="contact-row" style="top:4651px"><span class="icon"><svg width="20" height="20" viewBox="0 0 24 24"><path d="M6 3l4 4-2 3a12 12 0 0 0 6 6l3-2 4 4-3 3C10 21 3 14 3 6z" fill="none" stroke="#fff" stroke-width="2"/></svg></span>506-555-0147</div>
    <span class="social" style="left:28px;background:#1877f2" role="img" aria-label="Social link"></span>
    <span class="social" style="left:77px;background:#1da1f2" role="img" aria-label="Social link"></span>
    <span class="social" style="left:128px;background:#d6336c" role="img" aria-label="Social link"></span>

    <nav class="foot-nav">
      <a class="active">Home</a><a>Cruises</a><a>Adventures Tours</a><a>Custom Tours</a><a>Testimonials</a><a>About</a>
    </nav>

    <h3 class="form-title">Contact Us</h3>
    <span class="label" style="left:925px;top:4456px">First Name</span>
    <span class="label" style="left:1061px;top:4456px">Last Name</span>
    <div class="field" style="left:925px;top:4472px;width:97px"></div>
    <div class="field" style="left:1061px;top:4472px;width:99px"></div>
    <span class="label" style="left:925px;top:4523px">Email *</span>
    <span class="label" style="left:1061px;top:4523px">Subject</span>
    <div class="field" style="left:925px;top:4539px;width:97px"></div>
    <div class="field" style="left:1061px;top:4539px;width:99px"></div>
    <span class="label" style="left:925px;top:4590px">Message *</span>
    <div class="field" style="left:925px;top:4606px;width:235px;height:49px"></div>
    <div class="btn-teal submit">Submit</div>
  </footer>

</div>
</body>
</html>
```